BOLD & MINIMALIST DESIGN NEEDED

We want a very bold but minimalistic business card design that is impactful and utilizes both sides of the business card. Our current logo is included for your use.

We want bold fonts and good use of negative space. We don't want the logo to overpower the design.

Target Market(s)

Professionals who are building new commercial buildings.

Industry/Entity Type

Construction

Contact Information for Business Card

Name, Title, email, office phone, cell phone, website

Font styles to use
Serif
Sans Serif

Requirements
Must have
• Bold design!

```html
<!DOCTYPE html>
<html lang="en">
<head>
<meta charset="utf-8">
<title>Ridgeline Build Co – Business Card</title>
<link rel="stylesheet" href="https://fonts.googleapis.com/css2?family=Roboto:wght@500;700;900&display=swap">
<style>
  :root {
    --backdrop: #dfe4e2;
    --card: #ffffff;
    --ink: #111111;
    --text: #4a4a4a;
    --accent: #7dc242;
  }
  * { margin: 0; padding: 0; box-sizing: border-box; }
  html, body {
    width: 1200px;
    height: 716px;
    overflow: hidden;
    background: var(--backdrop);
    font-family: "Roboto", Arial, sans-serif;
  }
  .card {
    position: absolute;
    left: 369px;
    width: 461px;
    height: 264px;
    background: var(--card);
    border-radius: 14px;
    box-shadow: 0 1px 3px rgba(0,0,0,0.12);
  }
  .card--front { top: 94px; }
  .card--back { top: 382px; }

  .wordmark {
    display: flex;
    align-items: center;
    gap: 10px;
    color: var(--ink);
    font-weight: 900;
    text-transform: uppercase;
    white-space: nowrap;
  }
  .wordmark__square {
    background: var(--accent);
    flex: none;
  }
  .card--front .wordmark {
    position: absolute;
    left: 50%;
    top: 50%;
    transform: translate(-50%, -58%);
    font-size: 34px;
    letter-spacing: 0.5px;
  }
  .card--front .wordmark__square { width: 26px; height: 26px; }

  .card--back .wordmark {
    position: absolute;
    right: 19px;
    top: 66px;
    font-size: 14px;
    gap: 6px;
  }
  .card--back .wordmark__square { width: 12px; height: 12px; }

  .person {
    position: absolute;
    left: 16px;
    top: 28px;
    color: var(--text);
  }
  .person__name {
    font-size: 17px;
    font-weight: 700;
    letter-spacing: 0.1px;
    line-height: 20px;
  }
  .person__title {
    font-size: 13px;
    font-weight: 700;
    line-height: 16px;
    margin-top: 2px;
  }
  .person__rule {
    width: 16px;
    height: 4px;
    background: var(--ink);
    margin-top: 8px;
  }

  .contact {
    position: absolute;
    bottom: 20px;
    color: var(--text);
    font-size: 13px;
    font-weight: 700;
    line-height: 16.6px;
  }
  .contact--left { left: 16px; }
  .contact--right { right: 20px; text-align: right; }
</style>
</head>
<body>
  <section class="card card--front">
    <div class="wordmark"><span class="wordmark__square"></span>Ridgeline Build Co</div>
  </section>

  <section class="card card--back">
    <div class="person">
      <div class="person__name">DANA MORROW</div>
      <div class="person__title">Designer</div>
      <div class="person__rule"></div>
    </div>

    <div class="wordmark"><span class="wordmark__square"></span>Ridgeline Build Co</div>

    <div class="contact contact--left">
      <p>P : +1 555-014-2290</p>
      <p>E : dana@ridgebuild.co</p>
      <p>W : www.ridgebuild.co</p>
    </div>
    <div class="contact contact--right">
      <p>A : 48 Harbor Street</p>
      <p>Suite 12, Portland, OR</p>
    </div>
  </section>
</body>
</html>
```